Varentoria Business Card and Letter Head

We are a leadership assessment consultancy based in Sydney, Australia. We help executive-level decison-makers select leaders for more senior level roles in corporate and government organisations. Our methodology is based on the latest research from the field of neuroscience.
We need a business card design and matching letter head that presents our company, Varentoria, as a:
1. trusted adviser to senior executive-level decison makers
2. niche consultancy who are experts in the field of assessing leadership talent
3. results-focused solution provider who balance scientific methods with pragmatic solutions
The following company details should be used in all designs:
Company Name: Varentoria
Details (for business card):
Derek Hanford
Prime Capacity Officer
Level 29, Marlow Tower
7 Marlow Square
Sydney, NSW 2000 Australia
Phone: 1300 582 714
Mobile: 0412 637 258
Email: derek.hanford@varentoria-example.com.au
Website: varentoria-example.com.au
I have attached the logo for Varentoria (for both a white and black background) - your business card and letter head designs must incoporate this logo and colour scheme.
Thanks for your interest in this project, I'm looking forward to receiving your ideas.
Regards,
Derek
Target Market(s)
Executive-level decison-makers in corporate and government organisations (e.g., CEO, VP, Head of Human Resources)
Industry/Entity Type
Leadership
Look and feel

```html
<!DOCTYPE html>
<html lang="en">
<head>
<meta charset="utf-8">
<title>Varentoria Business Card</title>
<link rel="stylesheet" href="https://fonts.googleapis.com/css2?family=Questrial&family=PT+Sans:wght@400;700&display=swap">
<style>
  :root {
    --backdrop: #ececec;
    --card: #ffffff;
    --ink: #3d3d3d;
    --ink-soft: #555555;
    --accent: #b0231b;
    --faint: #ebebeb;
  }
  * { margin: 0; padding: 0; box-sizing: border-box; }
  html, body {
    width: 1200px; height: 469px; overflow: hidden;
    background: var(--backdrop);
  }
  .stage { position: relative; width: 1200px; height: 469px; }
  .card {
    position: absolute; top: 83px;
    width: 525px; height: 299px;
    background: var(--card);
    box-shadow: 0 2px 6px rgba(0,0,0,0.12);
  }
  .card--front { left: 55px; }
  .card--back { left: 610px; }

  .brand { position: absolute; display: flex; align-items: center; gap: 14px; }
  .brand__square { width: 40px; height: 40px; background: var(--ink); }
  .brand__name {
    font-family: "Questrial", sans-serif;
    font-size: 38px; color: var(--ink); line-height: 1;
  }
  .card--front .brand { left: 36px; top: 50px; }
  .card--back .brand { left: 98px; top: 114px; }

  .address, .contacts {
    position: absolute; left: 110px;
    font-family: "PT Sans", sans-serif;
    font-size: 12px; line-height: 17px; color: var(--ink-soft);
    list-style: none;
  }
  .address { top: 143px; }
  .contacts { top: 208px; }
  .contacts li { display: flex; align-items: center; gap: 8px; }
  .contacts svg { width: 10px; height: 10px; fill: var(--ink-soft); flex: none; }

  .backdrop-mark {
    position: absolute; left: 358px; top: 155px;
    width: 115px; height: 115px; background: var(--faint);
  }
  .person { position: absolute; left: 362px; top: 209px; font-family: "PT Sans", sans-serif; }
  .person__name { font-weight: 700; font-size: 15px; color: var(--accent); line-height: 18px; }
  .person__role { font-size: 12px; color: #222; line-height: 15px; }

  .web {
    position: absolute; left: 0; right: 0; top: 233px; text-align: center;
    font-family: "PT Sans", sans-serif; font-size: 13px; color: var(--ink);
  }
  .web__domain { color: var(--accent); }
</style>
</head>
<body>
<main class="stage">
  <section class="card card--front">
    <div class="brand">
      <span class="brand__square"></span>
      <span class="brand__name">Varentoria</span>
    </div>
    <address class="address">
      Level 29, Marlow Tower<br>
      7 Marlow Square<br>
      Sydney, NSW 2000 Australia
    </address>
    <ul class="contacts">
      <li><svg viewBox="0 0 10 10"><path d="M2 0.5 L3.8 2.6 L2.8 3.8 Q4 6 6.2 7.2 L7.4 6.2 L9.5 8 L8.2 9.5 Q3.5 9 0.5 1.8 Z"/></svg>1300 582 714</li>
      <li><svg viewBox="0 0 10 10"><path d="M2.5 0 H7.5 V10 H2.5 Z M3.5 1.2 V6.5 H6.5 V1.2 Z"/></svg>0412 637 258</li>
      <li><svg viewBox="0 0 10 10"><path d="M0.5 2 H9.5 V8 H0.5 Z M1 2.3 L5 5.3 L9 2.3 Z" /></svg>derek.hanford@varentoria-example.com.au</li>
      <li><svg viewBox="0 0 10 10"><circle cx="5" cy="5" r="4.6"/></svg>www.varentoria-example.com.au</li>
    </ul>
    <div class="backdrop-mark" aria-hidden="true"></div>
    <div class="person">
      <p class="person__name">Derek Hanford</p>
      <p class="person__role">Prime Capacity Officer</p>
    </div>
  </section>

  <section class="card card--back">
    <div class="brand">
      <span class="brand__square"></span>
      <span class="brand__name">Varentoria</span>
    </div>
    <p class="web">www.<span class="web__domain">varentoria-example</span>.com.au</p>
  </section>
</main>
</body>
</html>
```